Yacht, Boats, Watersports company needs a redesign of business card

Hello Designers!
We are a Boat dealership company that sells fun in the water, we sell boats, Yachts, Kayaks and also yacht WaterSport toys. We are looking to redesign our business cards in to something a little bit more sophisticated. in a way that we can make better use of our company colors. I'm attaching a zipped file containing the company 3 sets of company logo which one is an horizontal another one is a vertical and also a chromed 3d logo. Also is included two set of business cards that we use and also some designs that i think it's interesting. We use PMS 2026c Orange and PMS 7687C Blue. I would like to see at least two different options with the orange as accent and also using blue as an accent color. It's really important for the business cards to have a font option and size that is legible to most people. Our current website is wwww.coralpennant.com. Please visit if you want to have a better feeling of the Boat dealership
You can send Single sided or double side options. We are now using single sided but we may be open for a double side option if we really like the design.
Target Market(s)
Marine, boat sales, yacht sales, water toys sales/
Contact Information for Business Card
Name: Dale Whitcombe
Address: 212 North Fenwick Lane,
Harbor Point, FL 33190
Phone: 954-731-8842
Fax: 954:731-8843
Cell: 954-382-1490
Email: dw@coralpennant.com
Website: coralpennant.com
Requirements
Must have
- the current information of the business card provided.
logo
use the PMS Colors
Nice to have
- a touch of elegance and sophistication but simple
Should not have
- should not have any typography that is hard to read, the card should be simple but yet sophisticated.

```html
<!DOCTYPE html>
<html lang="en">
<head>
<meta charset="utf-8">
<title>Coral Pennant – Business Card</title>
<link rel="stylesheet" href="https://fonts.googleapis.com/css2?family=Montserrat:wght@500;600;700&display=swap">
<style>
  :root {
    --orange: #e2673a;
    --blue: #1f4f86;
    --blue-card: #2c5b8e;
    --white: #f6f6f4;
    --stage: #2b2b2d;
    --soft-white: #e9eef5;
  }
  * { margin: 0; padding: 0; box-sizing: border-box; }
  html, body { width: 1200px; height: 1000px; overflow: hidden; }
  body {
    background: var(--stage);
    font-family: "Montserrat", "Century Gothic", sans-serif;
    display: flex;
    align-items: center;
    justify-content: center;
    gap: 80px;
  }
  .card {
    width: 360px;
    height: 630px;
    border-radius: 22px;
    position: relative;
    overflow: hidden;
  }

  /* Front */
  .card-front { background: var(--white); }
  .front-mark {
    position: absolute;
    top: 48px; left: 50%;
    transform: translateX(-50%);
  }
  .front-company {
    position: absolute;
    top: 292px; width: 100%;
    text-align: center;
    color: var(--blue);
    font-weight: 700;
    font-size: 25px;
    letter-spacing: 2px;
  }
  .name-band {
    position: absolute;
    top: 350px; left: 0; width: 100%; height: 84px;
    background: var(--orange);
    display: flex; align-items: center; justify-content: center;
  }
  .person-name {
    color: var(--blue);
    font-weight: 700;
    font-size: 28px;
    letter-spacing: 0.5px;
  }
  .address {
    position: absolute;
    top: 466px; width: 100%;
    text-align: center;
    color: var(--blue);
    font-weight: 700;
    font-size: 21px;
    line-height: 1.45;
  }

  /* Back */
  .card-back { background: var(--blue-card); color: var(--soft-white); }
  .contact-group { position: absolute; left: 0; width: 100%; text-align: center; }
  .phones { top: 70px; }
  .online { top: 250px; }
  .icon-row { display: block; margin: 0 auto 16px; }
  .contact-line {
    font-weight: 500;
    font-size: 19px;
    letter-spacing: 2px;
    line-height: 1.6;
  }
  .contact-line.accent { font-size: 17px; letter-spacing: 1px; }
  .contact-line .domain { color: var(--orange); }
  .back-lockup {
    position: absolute;
    bottom: 60px; left: 0; width: 100%;
    display: flex; align-items: center; justify-content: center; gap: 16px;
  }
  .back-company {
    color: var(--white);
    font-weight: 700;
    font-size: 24px;
    letter-spacing: 2px;
    line-height: 1.1;
  }
</style>
</head>
<body>

  <article class="card card-front">
    <svg class="front-mark" width="200" height="200" viewBox="0 0 200 200" aria-hidden="true">
      <circle cx="100" cy="100" r="84" fill="none" stroke="var(--orange)" stroke-width="20"/>
    </svg>
    <p class="front-company">CORAL PENNANT</p>
    <div class="name-band"><h1 class="person-name">DALE WHITCOMBE</h1></div>
    <p class="address">212 North Fenwick Lane,<br>Harbor Point, FL 33190</p>
  </article>

  <article class="card card-back">
    <div class="contact-group phones">
      <svg class="icon-row" width="120" height="30" viewBox="0 0 120 30" aria-hidden="true">
        <line x1="20" y1="15" x2="100" y2="15" stroke="var(--orange)" stroke-width="2"/>
        <circle cx="20" cy="15" r="12" fill="var(--orange)"/>
        <circle cx="60" cy="15" r="12" fill="var(--orange)"/>
        <circle cx="100" cy="15" r="12" fill="var(--orange)"/>
        <path d="M15 9 q-2 8 8 12 l2 -3 -3 -2 -2 1 q-3 -2 -3 -5 l1 -2 -2 -3z" fill="var(--white)"/>
        <rect x="56" y="7" width="8" height="16" rx="1.5" fill="none" stroke="var(--white)" stroke-width="1.8"/>
        <rect x="94" y="11" width="12" height="9" rx="1" fill="var(--white)"/>
        <rect x="97" y="7" width="6" height="5" fill="none" stroke="var(--white)" stroke-width="1.5"/>
      </svg>
      <p class="contact-line">954-731-8842</p>
      <p class="contact-line">954-382-1490</p>
      <p class="contact-line">954:731-8843</p>
    </div>

    <div class="contact-group online">
      <svg class="icon-row" width="80" height="30" viewBox="0 0 80 30" aria-hidden="true">
        <line x1="20" y1="15" x2="60" y2="15" stroke="var(--orange)" stroke-width="2"/>
        <circle cx="20" cy="15" r="12" fill="var(--orange)"/>
        <circle cx="60" cy="15" r="12" fill="var(--orange)"/>
        <rect x="13" y="10" width="14" height="10" fill="none" stroke="var(--white)" stroke-width="1.6"/>
        <path d="M13 10 l7 6 7 -6" fill="none" stroke="var(--white)" stroke-width="1.6"/>
        <circle cx="60" cy="15" r="7" fill="none" stroke="var(--white)" stroke-width="1.5"/>
        <line x1="53" y1="15" x2="67" y2="15" stroke="var(--white)" stroke-width="1.3"/>
        <ellipse cx="60" cy="15" rx="3" ry="7" fill="none" stroke="var(--white)" stroke-width="1.3"/>
      </svg>
      <p class="contact-line accent">dw@<span class="domain">coralpennant.com</span></p>
      <p class="contact-line accent">www.<span class="domain">coralpennant.com</span></p>
    </div>

    <div class="back-lockup">
      <svg width="56" height="56" viewBox="0 0 56 56" aria-hidden="true">
        <circle cx="28" cy="28" r="23" fill="none" stroke="var(--white)" stroke-width="6"/>
      </svg>
      <p class="back-company">CORAL<br>PENNANT</p>
    </div>
  </article>

</body>
</html>
```